Simple Business Card Design for Tavlo

Job:

Make a very simple, minimalist business card design with my details including adjusted logo. One side to be white (with logo & text). Other side to be yellow - try plain or with logo (or part of logo eg Z). Need business card to have continuity with website.

Logo:
Our logo is made from a free download font website:
http://www.typewell.net/search.php?q=rubber
but the spacing/kerning needs correcting/adjusting as the font spaces unevenly between letters (see attached files). Need logo to be very crisp/sharp when printed.

Printing:
We will be using Plika.com so the design needs to conform to their requirements, see here:

http://uk.plika.com/products/luxe/business-cards.html (scroll down for dimensions and guidelines)

Design:

must say "plant-based food consulting" underneath logo or somewhere
no address needed in contact section
sharp corners (not rounded)
one side white, one side yellow

name: Rosalind Whitcombe
1xmobile number: +44 7700900463
1xtwiiter: @brimcounsel
website address www.orchardtable.com
email address brim@orchardtable.com

Should be easy quick job, prompt + detailed feedback given, am online in UK 9am-10pm for next 3 days. Website is www.orchardtable.com

Industry/Entity Type

Business

Requirements
Must have
• The logo must be corrected. The kerning is not right.

Please use a warm-grey for text

Please submit in matt format, we will be printing matt finish.

Should not have
• Avoid using banners or curvy highlights

Please avoid using black

Please avoid submitting in gloss finish

```html
<!DOCTYPE html>
<html lang="en">
<head>
<meta charset="utf-8">
<title>BRIM business card, front and back</title>
<link rel="stylesheet" href="https://fonts.googleapis.com/css2?family=Cinzel:wght@400;600;700&display=swap">
<style>
  :root {
    --backdrop: #e7e7e6;
    --card-white: #fbfbfa;
    --brand-yellow: #ecd93a;
    --yellow-light: #f7ee8e;
    --yellow-deep: #efdc42;
    --warm-grey: #5e5955;
    --warm-grey-soft: #6d6762;
  }
  * { margin: 0; padding: 0; box-sizing: border-box; }
  html, body {
    width: 1200px;
    height: 720px;
    overflow: hidden;
    background: var(--backdrop);
  }
  .canvas {
    position: relative;
    width: 1200px;
    height: 720px;
    font-family: "Cinzel", Georgia, serif;
    color: var(--warm-grey);
  }
  .card {
    position: absolute;
    top: 242px;
    width: 420px;
    height: 238px;
  }
  .card--front {
    left: 147px;
    background: var(--card-white);
  }
  .card--back {
    left: 633px;
    background: linear-gradient(120deg, var(--yellow-light) 0%, var(--yellow-deep) 100%);
  }
  .brand-name {
    font-family: "Cinzel", Georgia, serif;
    font-weight: 400;
    line-height: 1;
    letter-spacing: 2px;
  }
  .card--front .brand-name {
    position: absolute;
    left: 27px;
    top: 24px;
    font-size: 58px;
    color: var(--brand-yellow);
  }
  .contact-list {
    position: absolute;
    left: 23px;
    top: 171px;
    list-style: none;
  }
  .contact-item {
    display: flex;
    align-items: center;
    height: 12px;
    font-size: 9.5px;
    color: var(--warm-grey-soft);
    letter-spacing: 0.1px;
  }
  .contact-icon {
    width: 9px;
    height: 9px;
    margin-right: 9px;
    flex: none;
  }
  .holder-name {
    position: absolute;
    right: 16px;
    bottom: 27px;
    font-size: 13px;
    font-weight: 700;
    color: var(--warm-grey);
    font-variant: small-caps;
    letter-spacing: 0.3px;
  }
  .card--back .brand-block {
    position: absolute;
    left: 0;
    right: 0;
    top: 72px;
    text-align: center;
  }
  .card--back .brand-name {
    font-size: 72px;
    font-weight: 600;
    color: var(--warm-grey);
  }
  .tagline {
    margin-top: 10px;
    font-size: 12px;
    font-weight: 700;
    letter-spacing: 0.2px;
    color: var(--warm-grey);
  }
</style>
</head>
<body>
<main class="canvas">
  <section class="card card--front" aria-label="Card front">
    <div class="brand-name">BRIM</div>
    <ul class="contact-list">
      <li class="contact-item">
        <svg class="contact-icon" viewBox="0 0 10 10" aria-hidden="true">
          <path d="M1 3.5 Q5 0.5 9 3.5 L8 5 L6.5 4 L6.5 3 Q5 2.4 3.5 3 L3.5 4 L2 5 Z" fill="var(--brand-yellow)"/>
          <rect x="2.2" y="5.5" width="5.6" height="3.5" rx="0.6" fill="var(--brand-yellow)"/>
        </svg>
        +44 7700900463
      </li>
      <li class="contact-item">
        <svg class="contact-icon" viewBox="0 0 10 10" aria-hidden="true">
          <rect x="0.5" y="2" width="9" height="6.5" fill="var(--brand-yellow)"/>
          <path d="M0.8 2.4 L5 5.8 L9.2 2.4" fill="none" stroke="var(--card-white)" stroke-width="0.9"/>
        </svg>
        BRIM@ORCHARDTABLE.COM
      </li>
      <li class="contact-item">
        <svg class="contact-icon" viewBox="0 0 10 10" aria-hidden="true">
          <rect x="0.5" y="0.5" width="9" height="9" rx="1.5" fill="var(--brand-yellow)"/>
          <circle cx="5" cy="5" r="2.2" fill="var(--card-white)"/>
        </svg>
        @BRIMCOUNSEL
      </li>
      <li class="contact-item">
        <svg class="contact-icon" viewBox="0 0 10 10" aria-hidden="true">
          <rect x="0.8" y="1.2" width="8.4" height="5.8" fill="none" stroke="var(--brand-yellow)" stroke-width="1.1"/>
          <path d="M3.5 9 L6.5 9 M5 7 L5 9" stroke="var(--brand-yellow)" stroke-width="1.1"/>
        </svg>
        WWW.ORCHARDTABLE.COM
      </li>
    </ul>
    <div class="holder-name">Rosalind Whitcombe</div>
  </section>

  <section class="card card--back" aria-label="Card back">
    <div class="brand-block">
      <div class="brand-name">BRIM</div>
      <div class="tagline">PLANT-BASED FOOD CONSULTING</div>
    </div>
  </section>
</main>
</body>
</html>
```